Pepper & Palm Business Card FUN & EXCITING

Here is the Information for the Card:
Jaswinder Bains (Ravi)
E: RaviBains@postlark.com
C: (480) 555-0147
www.PepperPalmLV.com

We don't want traditional Indian cliche, We a playful bold and fun business card.

Files: https://files.cloudvessel.net/share/folders/7TqRmXpZ2vKa9LwBn4YcHd3JsEf6UoGi?usp=share_link

https://files.cloudvessel.net/share/folders/4MzXaQ8rTw2YbNcVk6PsLe5GhJdR3FoU?usp=share_link

Target Market(s)

Las Vegas Local Restaurant

Industry/Entity Type

Indian Restaurant

Contact Information for Business Card

Name, Email, Cell Phone, Company Logo

```html
<!DOCTYPE html>
<html lang="en">
<head>
<meta charset="utf-8">
<title>Pepper &amp; Palm — Business Card</title>
<link rel="stylesheet" href="https://fonts.googleapis.com/css2?family=Courier+Prime:wght@400;700&display=swap">
<style>
  :root {
    --stage: #2a2a2a;
    --magenta: #e0195f;
    --magenta-deep: #d81b60;
    --sun: #f2c313;
    --tangerine: #ee7a2a;
    --rose: #e8485a;
    --white: #ffffff;
    --pink-soft: #e8739a;
    --ink: #1a1a1a;
  }
  * { box-sizing: border-box; margin: 0; padding: 0; }
  html, body {
    width: 1200px; height: 1015px; overflow: hidden;
    background: var(--stage);
    font-family: "Courier Prime", "Courier New", monospace;
  }
  .canvas {
    width: 1200px; height: 1015px;
    display: flex; flex-direction: column; align-items: center; justify-content: center;
    gap: 56px;
  }
  .card {
    position: relative;
    width: 700px; height: 400px;
    overflow: hidden;
    border-radius: 4px;
    box-shadow: 0 12px 30px rgba(0,0,0,.45);
  }

  /* Front side */
  .card--front {
    background: linear-gradient(172deg, var(--magenta) 0 50%, var(--sun) 50% 100%);
  }
  .card--front .brand-name {
    position: absolute; left: 0; right: 0; top: 46px;
    text-align: center;
    font-weight: 700; font-size: 50px; letter-spacing: 1px;
    color: var(--white);
    text-transform: uppercase;
  }
  .card--front .mascot-art {
    position: absolute; left: 110px; width: 500px; top: 150px; height: 230px;
    border-radius: 120px 120px 40px 40px;
    background: linear-gradient(160deg, #fbf2d6 0%, #ffffff 40%, #f3a23c 80%, #ee7a2a 100%);
  }
  .sparkle {
    position: absolute; width: 26px; height: 26px;
  }
  .sparkle--a { left: 560px; top: 120px; }
  .sparkle--b { left: 70px; top: 300px; }
  .heart {
    position: absolute; width: 34px; height: 30px;
  }
  .heart--a { left: 630px; top: 140px; }
  .heart--b { left: 40px; top: 250px; }

  /* Back side */
  .card--back {
    background: linear-gradient(to top, var(--magenta-deep) 0%, var(--rose) 40%, var(--tangerine) 72%, var(--sun) 100%);
  }
  .card--back .mascot-art {
    position: absolute; left: 400px; right: 0; top: 30px; height: 250px;
    border-radius: 120px 0 0 60px;
    background: linear-gradient(150deg, #ffffff 0%, #fdf0e0 45%, #f08a2e 100%);
  }
  .card--back .brand-name {
    position: absolute; left: 40px; top: 140px;
    font-weight: 700; font-size: 28px; letter-spacing: .5px;
    color: var(--white);
    text-transform: uppercase;
  }
  .contact {
    position: absolute; left: 40px; top: 200px;
    color: var(--white);
  }
  .contact__name {
    font-weight: 700; font-size: 22px; letter-spacing: .5px;
  }
  .contact__rule {
    width: 70px; height: 1px; margin: 12px 0 14px;
    background: var(--sun);
  }
  .contact__list { list-style: none; display: flex; flex-direction: column; gap: 10px; }
  .contact__item {
    display: flex; align-items: center; gap: 14px;
    font-size: 16px;
  }
  .contact__icon { width: 34px; height: 30px; flex: none; }
</style>
</head>
<body>
<main class="canvas">

  <section class="card card--front" aria-label="Card front">
    <div class="brand-name">Pepper &amp; Palm</div>
    <div class="mascot-art" role="img" aria-label="Cartoon illustration of a smiling curry bowl and a piece of flatbread walking together"></div>
    <svg class="sparkle sparkle--a" viewBox="0 0 26 26" aria-hidden="true"><path d="M13 0L16 10 26 13 16 16 13 26 10 16 0 13 10 10Z" fill="#1a1a1a"/></svg>
    <svg class="sparkle sparkle--b" viewBox="0 0 26 26" aria-hidden="true"><path d="M13 0L16 10 26 13 16 16 13 26 10 16 0 13 10 10Z" fill="#1a1a1a"/></svg>
    <svg class="heart heart--a" viewBox="0 0 34 30" aria-hidden="true"><path d="M17 29 C4 20 1 14 1 9 A8 8 0 0 1 17 6 A8 8 0 0 1 33 9 C33 14 30 20 17 29Z" fill="#e8739a"/></svg>
    <svg class="heart heart--b" viewBox="0 0 34 30" aria-hidden="true"><path d="M17 29 C4 20 1 14 1 9 A8 8 0 0 1 17 6 A8 8 0 0 1 33 9 C33 14 30 20 17 29Z" fill="#e8739a"/></svg>
  </section>

  <section class="card card--back" aria-label="Card back">
    <div class="mascot-art" role="img" aria-label="Cartoon illustration of a curry bowl character pointing and walking"></div>
    <div class="brand-name">Pepper &amp; Palm</div>
    <div class="contact">
      <p class="contact__name">Jaswinder Bains (Ravi)</p>
      <div class="contact__rule"></div>
      <ul class="contact__list">
        <li class="contact__item">
          <svg class="contact__icon" viewBox="0 0 34 30" aria-hidden="true">
            <path d="M17 29 C4 20 1 14 1 9 A8 8 0 0 1 17 6 A8 8 0 0 1 33 9 C33 14 30 20 17 29Z" fill="#f2c313"/>
            <circle cx="17" cy="13" r="6.5" fill="none" stroke="#e0195f" stroke-width="1.6"/>
            <path d="M10.5 13h13M17 6.5c-3 3.5-3 9.5 0 13M17 6.5c3 3.5 3 9.5 0 13" fill="none" stroke="#e0195f" stroke-width="1.3"/>
          </svg>
          <span>www.PepperPalmLV.com</span>
        </li>
        <li class="contact__item">
          <svg class="contact__icon" viewBox="0 0 34 30" aria-hidden="true">
            <path d="M17 29 C4 20 1 14 1 9 A8 8 0 0 1 17 6 A8 8 0 0 1 33 9 C33 14 30 20 17 29Z" fill="#f2c313"/>
            <rect x="9.5" y="8" width="15" height="10" fill="none" stroke="#e0195f" stroke-width="1.6"/>
            <path d="M9.5 8l7.5 6 7.5-6" fill="none" stroke="#e0195f" stroke-width="1.6"/>
          </svg>
          <span>RaviBains@postlark.com</span>
        </li>
        <li class="contact__item">
          <svg class="contact__icon" viewBox="0 0 34 30" aria-hidden="true">
            <path d="M17 29 C4 20 1 14 1 9 A8 8 0 0 1 17 6 A8 8 0 0 1 33 9 C33 14 30 20 17 29Z" fill="#f2c313"/>
            <path d="M12 8c-1.5 1-1.5 3 0 5.5s4.5 5 6.5 5.5c2 .5 3.5-.5 4-1.5l-2.5-2-1.5 1c-1.5-.5-3.5-2.5-4-4l1-1.5-2-2.5z" fill="none" stroke="#e0195f" stroke-width="1.5" stroke-linejoin="round"/>
          </svg>
          <span>(480) 555-0147</span>
        </li>
      </ul>
    </div>
  </section>

</main>
</body>
</html>
```